Business Card Design

We are a residential half way house for the addict ,the alcoholic and dual diagnosed in recovery.
i house both men and woman age 18+

Industry/Entity Type

Residential

```html
<!DOCTYPE html>
<html lang="en">
<head>
<meta charset="utf-8">
<title>Harbor Light Recovery Residence – Business Card</title>
<link href="https://fonts.googleapis.com/css2?family=Tinos&display=swap" rel="stylesheet">
<style>
  :root {
    --page: #e4e1dc;
    --frost-top: #f4f3f1;
    --frost-mid: #d9dde2;
    --frost-low: #eceae6;
    --ink: #141414;
    --band-dark: #2a2b2e;
    --band-grey: #5d6068;
    --name: #f1efec;
    --role: #dcdad6;
    --panel: #0b0b0b;
    --panel-glow: #3a3a3a;
    --tan: #d6c4ad;
    --rose: #c99a98;
    --rule: #1b1b1b;
    --rule-light: #c9c1b6;
  }
  html, body { margin: 0; padding: 0; }
  body {
    width: 1200px; height: 970px; overflow: hidden;
    background: var(--page);
    position: relative;
  }
  .card {
    position: absolute; left: 100px; top: 207px;
    width: 1000px; height: 556px;
    overflow: hidden;
    box-shadow: 0 10px 30px rgba(0,0,0,.25);
    font-family: "Tinos", "Times New Roman", serif;
  }
  .card__front {
    position: absolute; inset: 0 0 auto 0; height: 301px;
    background: linear-gradient(180deg, var(--frost-top) 0%, var(--frost-mid) 55%, var(--frost-low) 100%);
  }
  .name-ribbon { position: absolute; left: 0; top: 62px; }
  .name-ribbon__name {
    position: absolute; left: 70px; top: 70px;
    font-size: 34px; color: var(--name); letter-spacing: .3px; margin: 0; font-weight: 400;
  }
  .name-ribbon__role {
    position: absolute; left: 67px; top: 128px;
    font-size: 22px; color: var(--role); margin: 0;
  }
  .brand {
    position: absolute; right: 74px; top: 96px; text-align: right;
    font-family: "Tinos", "Times New Roman", serif;
    color: var(--ink); line-height: 1.1; margin: 0; font-weight: 400;
  }
  .brand__main { display: block; font-size: 62px; }
  .brand__sub { display: block; font-size: 30px; margin-top: 8px; letter-spacing: 1px; }
  .divider {
    position: absolute; left: 0; right: 0; top: 301px; height: 14px;
    background: var(--rule-light);
    border-top: 3px solid var(--rule); border-bottom: 3px solid var(--rule);
    box-sizing: border-box;
  }
  .divider::after {
    content: ""; position: absolute; left: 0; right: 0; top: 4px; height: 1px; background: var(--rule);
  }
  .card__contact {
    position: absolute; left: 0; right: 0; top: 315px; bottom: 0;
    background: radial-gradient(ellipse 60% 70% at 30% 10%, var(--panel-glow) 0%, var(--panel) 70%);
  }
  .contact-item {
    position: absolute; display: flex; align-items: center; gap: 18px;
    font-size: 23px; color: var(--tan);
  }
  .contact-item--email { color: var(--rose); }
  .contact-item svg { width: 32px; height: 30px; flex: none; }
  .address { position: absolute; left: 700px; top: 72px; font-size: 23px; color: var(--tan); line-height: 42px; margin: 0; }
</style>
</head>
<body>
<div class="card">
  <section class="card__front">
    <svg class="name-ribbon" width="470" height="100" viewBox="0 0 470 100" aria-hidden="true">
      <polygon points="0,0 305,0 468,62 0,62" fill="var(--band-dark)"/>
      <polygon points="0,50 392,50 354,100 0,100" fill="var(--band-grey)"/>
    </svg>
    <h1 class="name-ribbon__name">Marisol Reyes</h1>
    <p class="name-ribbon__role">Owner</p>
    <h2 class="brand">
      <span class="brand__main">Harbor Light</span>
      <span class="brand__sub">Recovery Residence LLC</span>
    </h2>
  </section>
  <div class="divider"></div>
  <section class="card__contact">
    <div class="contact-item" style="left:70px;top:78px">
      <svg viewBox="0 0 32 30" aria-hidden="true"><rect width="32" height="30" rx="6" fill="var(--tan)"/><path d="M7 12c0-4 18-4 18 0v2h-5v-2h-8v2H7z" fill="#222"/><rect x="9" y="15" width="14" height="8" rx="2" fill="#222"/><circle cx="16" cy="19" r="2" fill="var(--tan)"/></svg>
      <span>(555) 014-2270</span>
    </div>
    <div class="contact-item" style="left:70px;top:120px">
      <svg viewBox="0 0 32 30" aria-hidden="true"><rect width="32" height="30" rx="6" fill="var(--tan)"/><path d="M7 12c0-4 18-4 18 0v2h-5v-2h-8v2H7z" fill="#222"/><rect x="9" y="15" width="14" height="8" rx="2" fill="#222"/><circle cx="16" cy="19" r="2" fill="var(--tan)"/></svg>
      <span>(555) 014-2271</span>
    </div>
    <div class="contact-item" style="left:325px;top:78px">
      <svg viewBox="0 0 32 30" aria-hidden="true"><rect width="32" height="30" rx="6" fill="#e3d6d4"/><rect x="10" y="6" width="12" height="6" fill="#333"/><rect x="6" y="11" width="20" height="9" rx="2" fill="#333"/><rect x="10" y="17" width="12" height="7" fill="#fff" stroke="#333" stroke-width="1.5"/></svg>
      <span>(555) 019-3348</span>
    </div>
    <div class="contact-item contact-item--email" style="left:325px;top:120px">
      <svg viewBox="0 0 32 30" aria-hidden="true"><rect width="32" height="30" rx="6" fill="var(--rose)"/><path d="M6 13l10-7 10 7v10H6z" fill="none" stroke="#fff" stroke-width="2"/><path d="M6 13l10 6 10-6" fill="none" stroke="#fff" stroke-width="2"/></svg>
      <span>marisolreyes@example.com</span>
    </div>
    <svg style="position:absolute;left:650px;top:78px;width:32px;height:30px" viewBox="0 0 32 30" aria-hidden="true"><rect width="32" height="30" rx="6" fill="#6b6258"/><path d="M16 25c-5-6-7-9-7-12a7 7 0 0 1 14 0c0 3-2 6-7 12z" fill="#111"/><circle cx="16" cy="13" r="2.5" fill="#6b6258"/></svg>
    <p class="address">1478 Palmetto Ln.<br>Seabrook,Fla 33999</p>
  </section>
</div>
</body>
</html>
```